KLN Productions Biz Card 2014-1

I own a small business whose primary function is Professional Fashion and Commercial Photography and has a secondary function of Talent Management of Models/Actors. I've used Crelloband in the past to print my own design, but I'd like something a bit more topical, fresh and done by an artist instead of a photographer (me).

My company logo is included with a few selected horizontal (landscape) photos of some of my models--I'd like to use a single model photo as the background for the entire card, either in color or converted to black and white, at opacity enough to see the photo but not too much to obscure any text or the company logo, or use a photo as a share of the card (not the entire background), or use all the three models on the card in some manor... Our company colors are white, black, grey-silver and red.

Industry/Entity Type

Small Business

Contact Information for Business Card

Dorian Valstead, Owner
KLN Productions
PO Box 7316
Brattleboro VT 05871-7316
(472) 555-4172
dori@klnstudiosample,.com

```html
<!DOCTYPE html>
<html lang="en">
<head>
<meta charset="utf-8">
<title>KLN Productions – Business Card</title>
<link href="https://fonts.googleapis.com/css2?family=Lato:wght@400;700&display=swap" rel="stylesheet">
<style>
  :root{
    --bg:#e6e6e6;
    --card-black:#050505;
    --brand-red:#e8202a;
    --logo-white:#ffffff;
    --text-grey:#a9a9a9;
    --ink-dark:#3a3a3a;
    --ink-black:#111111;
  }
  *{box-sizing:border-box;margin:0;padding:0}
  html,body{width:1200px;height:926px;overflow:hidden;background:var(--bg);font-family:'Lato',sans-serif}
  .sheet{position:relative;width:1200px;height:926px}
  .card{position:absolute;left:240px;width:720px;height:411px;overflow:hidden;box-shadow:0 4px 14px rgba(0,0,0,.18)}
  .card--back{top:35px}
  .card--front{top:480px;background:var(--card-black)}

  /* back side */
  .model-collage{position:absolute;inset:0;
    background:linear-gradient(100deg,#5d7283 0%,#c9a58c 22%,#7d8fa8 40%,#3a3f4a 55%,#8a6fa0 62%,#cfb49a 78%,#b73a3a 100%)}
  .logo-band{position:absolute;left:360px;top:262px;width:360px;height:100px;background:var(--logo-white);
    display:flex;align-items:center;padding-left:28px}

  /* brand name */
  .brand-name{font-weight:700;color:var(--ink-dark);font-size:30px;letter-spacing:1px;white-space:nowrap}

  /* front side */
  .contact{position:absolute;left:30px;top:38px;width:360px;display:flex;flex-direction:column;align-items:center;gap:14px;color:var(--text-grey);font-size:19px;text-align:center;line-height:1.2}
  .contact__item{display:flex;flex-direction:column;align-items:center;gap:5px}
  .contact__icon{width:22px;height:22px;fill:none;stroke:var(--logo-white);stroke-width:1.6}
  .front-logo{position:absolute;left:400px;top:88px;width:290px;height:74px;background:var(--logo-white);
    display:flex;align-items:center;padding-left:22px}
  .front-logo .brand-name{font-size:24px}
  .nameplate{position:absolute;left:376px;top:280px;width:310px;height:104px;background:var(--brand-red);padding:26px 0 0 24px}
  .nameplate__name{color:var(--logo-white);font-size:25px;text-transform:uppercase;letter-spacing:.3px;white-space:nowrap}
  .nameplate__name b{font-weight:700}
  .nameplate__role{color:var(--ink-black);font-size:19px;font-weight:700;margin-left:76px;line-height:1.1}
</style>
</head>
<body>
<main class="sheet">

  <section class="card card--back" aria-label="Card back">
    <div class="model-collage" role="img" aria-label="Collage of model portrait photographs in diagonal strips"></div>
    <div class="logo-band">
      <span class="brand-name">KLN Productions</span>
    </div>
  </section>

  <section class="card card--front" aria-label="Card front">
    <div class="contact">
      <div class="contact__item">
        <svg class="contact__icon" viewBox="0 0 24 24"><path d="M3 8c0-3 18-3 18 0v2h-4V8H7v2H3z"/><rect x="5" y="12" width="14" height="9" rx="1"/><circle cx="12" cy="16.5" r="2"/></svg>
        <span>04871-7316</span>
      </div>
      <div class="contact__item">
        <svg class="contact__icon" viewBox="0 0 24 24"><rect x="6" y="2" width="12" height="20" rx="2"/><rect x="8" y="5" width="8" height="6"/><path d="M9 14h1M12 14h1M9 17h1M12 17h1"/></svg>
        <span>(472) 555-4172</span>
      </div>
      <div class="contact__item">
        <svg class="contact__icon" viewBox="0 0 24 24"><rect x="2" y="5" width="20" height="14"/><path d="M2 5l10 8 10-8"/></svg>
        <span>dori@klnstudiosample.com</span>
      </div>
      <div class="contact__item">
        <svg class="contact__icon" viewBox="0 0 24 24"><circle cx="12" cy="12" r="10"/><ellipse cx="12" cy="12" rx="4.5" ry="10"/><path d="M2 12h20M4 7h16M4 17h16"/></svg>
        <span>KLN Productions<br>PO Box 7316 Corvell Falls VT</span>
      </div>
    </div>

    <div class="front-logo">
      <span class="brand-name">KLN Productions</span>
    </div>

    <div class="nameplate">
      <p class="nameplate__name"><b>Dorian</b> Valstead</p>
      <p class="nameplate__role">owner</p>
    </div>
  </section>

</main>
</body>
</html>
```